Web Design job - NetKestrel Company including Desktop & Mobile version

Create a Web Design (Uncoded - PSD layout only)

1. About our company

NetKestrel is an Australian-based company which sells used networking devices to coporates and other brokers in USA, Europe and other countries. We are the market leader in this space and currently have warehouses in Sydney and California. Most of our products are from VORLAN.

Our competitive advantages come from lowest price in the market, flexible product configuration for different demands of customers, long time experience in the business and huge stock of inventory.

We are in need of a new website to enhance customer and partner engagement which are measured by sales metrics and website performance metrics such as number of request for a quote, number of new orders, return visits, views, conversion rate, etc.

2. Website structure:

We need different looks for different devices: Desktop, iPad and Mobile with popular screen resolutions for each of following page.

Try to make one as good as possible, then we can move further. Below are the main pages of the web:

+ Home Page: Where customers learn about the company and its business. Should have: Beautiful company profile, highlighted company contact and strengths; A comprehensive overview about selling products.

+ Category Page: Where customers learn about products in a category and do the search action. Should focus on filter and sort functions for easily finding a product.

+ Product Page: Where customers learn about the details of a specific products such as price, image, description, related products.
- Also need features for cross-sell or up-sell.
- An item may have both new and refurbished prices, or either or none of them. Should have options to choose between new or refurbished price to add to cart.

+ Information Page: About the company, Company Announcement.

+ Cart management and Check-out

+ Search results

REFERENCES
Current website: http://netkestrel.com.au/

Prefered Layout:
- https://www.gearbazaar-example.com/en/vorlan-systems/vorlan-router-series/vorlan-series-1900/vorlan-systems-vorlan1941-k9
- https://www.wiresandboxes-example.com/vorlan-2port-rj48-multiflex-t1-trunk-card-vwic2mftt1-p-1374.html
- The attached files play as wireframes, only for the purpose of guiding. You are free to make your choices of colors and layouts.

Target Market(s)

- Corporate clients
- Main market: Australia

Industry/Entity Type

It Company

Number of Pages Required

3 page

Font styles to use
Sans Serif

Requirements
Must have
• - The new design should have a clear look to easily find information while should look professional to aim at corporate clients.
• - Require least time or effort to finish a task
• - Optimize for SEO and loading time
• - Mobile version is optimized for touching, swiping and loading time.
• - Bear in mind that the new website need minimum effort of manual tasks such as updating content. We don’t have human resources for these yet.
Nice to have
• - Should have design for each scenario such as click, popup, dropdown, deactive, have/not have an object

```html
<!DOCTYPE html>
<html lang="en">
<head>
<meta charset="utf-8">
<title>NetKestrel – Networking Equipment</title>
<link href="https://fonts.googleapis.com/css2?family=Oswald:wght@400;500&family=Roboto:wght@400;500;700&display=swap" rel="stylesheet">
<style>
:root{
  --red:#e1452f;
  --blue:#0c4fa3;
  --ink:#333333;
  --muted:#666666;
  --light:#f1f1f1;
  --grey:#e6e6e6;
  --line:#d6d6d6;
  --white:#ffffff;
}
*{box-sizing:border-box;margin:0;padding:0}
html,body{width:1200px;height:3830px;overflow:hidden}
body{font-family:"Roboto",Arial,sans-serif;color:var(--ink);background:var(--white);position:relative}
.wrap{width:1000px;margin:0 auto;position:relative}
svg{display:block}

/* header */
.site-header{height:122px;position:relative}
.brand{position:absolute;left:97px;top:28px;display:flex;align-items:center;gap:14px}
.brand-dot{width:62px;height:62px;border-radius:50%;background:var(--red)}
.brand-name{font-size:38px;font-weight:700;color:var(--blue);letter-spacing:-.5px}
.search{position:absolute;left:472px;top:41px;width:312px;height:41px;border:2px solid #bcbcbc;border-radius:21px;display:flex;align-items:center;font-size:12px;color:#555}
.search-input{flex:1;padding-left:18px}
.search-cat{width:104px;height:100%;border-left:1px solid #bcbcbc;border-right:1px solid #bcbcbc;display:flex;align-items:center;padding-left:8px}
.search-btn{width:46px;display:flex;justify-content:center}
.call{position:absolute;left:812px;top:40px;font-size:12px;color:#444}
.call strong{display:block;font-size:17px;color:#222;margin-top:6px;font-weight:500}
.cart{position:absolute;left:1000px;top:50px;display:flex;align-items:center;gap:10px;font-size:18px;color:#222}

.main-nav{height:54px;background:var(--red);display:flex;padding-left:100px}
.main-nav a{width:163px;color:var(--white);font-size:14px;font-weight:500;text-decoration:none;display:flex;align-items:center;justify-content:center}
.main-nav a.active{background:var(--blue)}

/* hero */
.hero{height:450px;background:var(--light);border:2px solid #dcdcdc;position:relative}
.hero-visual{position:absolute;left:102px;top:77px;width:460px;height:288px;background:linear-gradient(90deg,#2d2f33,#5b5f66 55%,#3a3c40)}
.hero-copy{position:absolute;left:671px;top:92px}
.hero-title{font-family:"Oswald",Arial,sans-serif;font-weight:500;font-size:52px;color:var(--red);line-height:1}
.hero-sub{font-size:15px;color:#444;margin-top:22px}
.btn-outline{display:inline-block;margin-top:42px;border:3px solid var(--red);color:var(--red);font-size:16px;font-weight:500;padding:14px 12px}
.dots{display:flex;gap:5px;margin-top:34px}
.dots span{width:14px;height:14px;border-radius:50%;border:1px solid #999}
.dots span.on{background:var(--red);border-color:var(--red)}

/* section headings */
.section-title{text-align:center;font-size:29px;font-weight:700;color:var(--red);letter-spacing:.3px}
.section-title.on-red{color:var(--white)}
.rule{width:86px;height:2px;background:var(--red);margin:22px auto 0}
.rule.on-red{background:var(--white)}

/* welcome */
.welcome{height:554px;padding-top:70px}
.welcome-text{width:940px;margin:34px auto 0;text-align:center;font-size:13px;line-height:29px;color:#444}
.stats{display:flex;justify-content:space-between;width:1000px;margin:50px auto 0;padding:0 20px}
.stat{width:225px;text-align:center}
.stat-ring{width:147px;height:147px;margin:0 auto;border-radius:50%;border:3px solid var(--red);display:flex;align-items:center;justify-content:center}
.stat-ring span{width:121px;height:121px;border-radius:50%;background:var(--red);color:var(--white);font-size:36px;font-weight:500;display:flex;align-items:center;justify-content:center}
.stat.blue .stat-ring{border-color:var(--blue)}
.stat.blue .stat-ring span{background:var(--blue)}
.stat-label{margin-top:20px;font-size:19px;line-height:28px;color:var(--red)}
.stat.blue .stat-label{color:var(--blue)}

/* product grids */
.categories{height:566px;background:var(--red);padding-top:53px}
.grid{display:flex;gap:20px;width:1000px;margin:0 auto}
.card{width:235px;text-align:center}
.card-media{height:197px;background:var(--white);border:1px solid var(--line);display:flex;align-items:center;justify-content:center}
.media-fill{width:170px;height:110px;border-radius:4px}
.fill-dark{background:linear-gradient(180deg,#3c3f44,#1f2124)}
.fill-light{background:linear-gradient(180deg,#f4f4f4,#cfd2d6)}
.fill-green{background:linear-gradient(180deg,#3f7a45,#23502a)}
.card-name{font-size:19px;margin-top:28px}
.categories .card-name{color:var(--white);font-size:18px;margin-top:24px}
.card-meta{display:flex;justify-content:center;gap:48px;font-size:13px;margin-top:14px;color:#444}
.categories .card-meta{color:#f9d5cf}
.card-price{font-size:20px;margin-top:14px}
.card-price s{font-size:16px;margin-right:8px}
.categories .card-price{color:var(--white)}
.categories .grid{margin-top:55px}

.new-products{height:592px;padding-top:64px}
.new-products .grid{margin-top:56px}
.new-products .card-name{font-size:20px;margin-top:26px}

.most-viewed{height:437px;background:var(--grey);padding-top:50px}
.most-viewed .grid{margin-top:53px}
.most-viewed .card-media{height:166px}
.most-viewed .card-name{font-size:16px;margin-top:24px}

/* quote */
.quote{height:539px;position:relative}
.quote-copy{position:absolute;left:100px;top:103px;width:350px}
.quote-title{font-size:29px;font-weight:700;color:var(--red)}
.quote-text{font-size:15px;line-height:30px;margin-top:50px}
.contact-row{display:flex;align-items:center;gap:16px;margin-top:20px;font-size:21px}
.contact-row.phone{color:var(--red)}
.contact-row.mail{color:var(--blue);font-weight:700}
.icon-circle{width:40px;height:40px;border-radius:50%;border:2px solid currentColor;display:flex;align-items:center;justify-content:center}
.or-mail{font-size:15px;margin-top:18px}
.quote-person{position:absolute;left:485px;top:71px;width:281px;height:468px;background:linear-gradient(180deg,#eef3f8,#b9cde3)}
.promo{position:absolute;left:802px;top:69px;width:298px;height:398px;background:var(--light);border:2px solid #d8d8d8;text-align:center}
.promo-visual{width:240px;height:120px;margin:40px auto 0;background:linear-gradient(90deg,#6d7178,#a8acb2,#55595f)}
.promo-title{font-family:"Oswald",Arial,sans-serif;font-size:38px;color:var(--red);margin-top:28px;line-height:1}
.promo-sub{font-family:"Oswald",Arial,sans-serif;font-size:26px;color:var(--red);margin-top:12px}
.promo-note{font-size:14px;line-height:26px;margin-top:20px}

/* link bar */
.link-bar{height:69px;display:flex}
.link-bar a{flex:1;display:flex;align-items:center;justify-content:center;position:relative;color:var(--white);font-size:24px;font-weight:700;text-decoration:none;background:var(--red);letter-spacing:.5px}
.link-bar a.blue{background:var(--blue)}
.link-bar svg{position:absolute;right:18px;top:24px}

/* footer */
.site-footer{height:447px;background:var(--grey);position:relative}
.footer-cols{position:absolute;left:100px;top:56px;display:flex;width:1000px}
.footer-col{width:386px}
.footer-col:last-child{width:228px}
.footer-title{font-size:19px;font-weight:700;color:var(--red)}
.footer-rule{width:48px;height:2px;background:var(--red);margin-top:14px}
.footer-text{font-size:13px;line-height:22px;width:258px;margin-top:30px;color:#444}
.footer-text + .footer-text{margin-top:10px}
.pay{display:flex;gap:10px;margin-top:22px}
.pay span{width:36px;height:22px;border-radius:3px}
.footer-list{list-style:none;margin-top:32px}
.footer-list li{display:flex;align-items:flex-start;gap:16px;font-size:13px;line-height:20px;margin-bottom:18px;color:#333}
.footer-list .ic{flex:none;width:28px;height:28px;border-radius:50%;border:1px solid #555;display:flex;align-items:center;justify-content:center}
.footer-list span.txt{padding-top:4px}
.footer-bottom{position:absolute;left:100px;top:350px;width:1000px;border-top:1px solid #999;text-align:center;padding-top:46px;font-size:15px;color:#333}
</style>
</head>
<body>

<header class="site-header">
  <div class="brand"><span class="brand-dot"></span><span class="brand-name">NetKestrel</span></div>
  <div class="search">
    <span class="search-input">Search...</span>
    <span class="search-cat">All Categories</span>
    <span class="search-btn"><svg width="14" height="14" viewBox="0 0 14 14"><circle cx="6" cy="6" r="4.5" fill="none" stroke="#333" stroke-width="1.8"/><line x1="9.3" y1="9.3" x2="13" y2="13" stroke="#333" stroke-width="1.8"/></svg></span>
  </div>
  <div class="call">CALL US NOW<strong>(+61) 02 5550 1470</strong></div>
  <div class="cart"><svg width="24" height="22" viewBox="0 0 24 22"><path d="M7 7V5a5 5 0 0 1 10 0v2" fill="none" stroke="#222" stroke-width="2"/><rect x="2" y="7" width="20" height="15" rx="1" fill="#222"/></svg>0 Items</div>
</header>

<nav class="main-nav">
  <a class="active">HOME</a><a>ROUTERS</a><a>SWITCHES</a><a>WIRELESSES</a><a>IP PHONES</a><a>ACCESSORIES</a>
</nav>

<section class="hero">
  <div class="hero-visual" role="img" aria-label="Rack-mounted network servers and routers"></div>
  <div class="hero-copy">
    <div class="hero-title">SAVE UP TO 40%</div>
    <p class="hero-sub">By doing business with NETKESTREL</p>
    <span class="btn-outline">REQUEST A QUOTE</span>
    <div class="dots"><span class="on"></span><span></span><span></span><span></span><span></span></div>
  </div>
</section>

<section class="welcome">
  <h2 class="section-title">WELCOME TO NETKESTREL</h2>
  <div class="rule"></div>
  <p class="welcome-text">NetKestrel is a network hardware reseller founded in 2010 and based in Kestrel Park, NSW. Trading in more than 80 countries, we have a strong profile on the markets for new and refurbished network equipments.</p>
  <div class="stats">
    <div class="stat"><div class="stat-ring"><span>7</span></div><p class="stat-label">Years Of<br>Experience</p></div>
    <div class="stat blue"><div class="stat-ring"><span>99.5%</span></div><p class="stat-label">Positive Feedback<br>On Tradeloft</p></div>
    <div class="stat"><div class="stat-ring"><span>300</span></div><p class="stat-label">Clients And Partners<br>Around The World</p></div>
    <div class="stat blue"><div class="stat-ring"><span>1.250</span></div><p class="stat-label">SKUs In Inventory</p></div>
  </div>
</section>

<section class="categories">
  <h2 class="section-title on-red">PRODUCT CATEGORIES</h2>
  <div class="rule on-red"></div>
  <div class="grid">
    <div class="card"><div class="card-media"><div class="media-fill fill-dark" role="img" aria-label="Wireless access points and security appliance"></div></div><p class="card-name">Wireless &amp; Securities</p><div class="card-meta"><span>Referbished</span><span>AS220</span></div><p class="card-price"><s>$ 90.00</s>$ 70.00</p></div>
    <div class="card"><div class="card-media"><div class="media-fill fill-dark" role="img" aria-label="Stacked routers and switches"></div></div><p class="card-name">Routers &amp; Switches</p><div class="card-meta"><span>Referbished</span><span>AS220</span></div><p class="card-price"><s>$ 90.00</s>$ 70.00</p></div>
    <div class="card"><div class="card-media"><div class="media-fill fill-light" role="img" aria-label="Desk IP phones"></div></div><p class="card-name">IP Phones</p><div class="card-meta"><span>Referbished</span><span>AS220</span></div><p class="card-price"><s>$ 90.00</s>$ 70.00</p></div>
    <div class="card"><div class="card-media"><div class="media-fill fill-light" role="img" aria-label="Transceiver modules and accessories"></div></div><p class="card-name">Accessories</p><div class="card-meta"><span>Referbished</span><span>AS220</span></div><p class="card-price"><s>$ 90.00</s>$ 70.00</p></div>
  </div>
</section>

<section class="new-products">
  <h2 class="section-title">NEW PRODUCTS</h2>
  <div class="rule"></div>
  <div class="grid">
    <div class="card"><div class="card-media"><div class="media-fill fill-light" role="img" aria-label="White wireless access point"></div></div><p class="card-name">VRL-OEAP6021-A-K9</p><div class="card-meta"><span>Referbished</span><span>AS220</span></div><p class="card-price"><s>$ 90.00</s>$ 70.00</p></div>
    <div class="card"><div class="card-media"><div class="media-fill fill-dark" role="img" aria-label="Black rack router"></div></div><p class="card-name">VRL-OEA25021-A-K9</p><div class="card-meta"><span>Referbished</span><span>AS220</span></div><p class="card-price"><s>$ 90.00</s>$ 70.00</p></div>
    <div class="card"><div class="card-media"><div class="media-fill fill-light" role="img" aria-label="Silver desktop router"></div></div><p class="card-name">VRL-ODIP6021-A-K9</p><div class="card-meta"><span>Referbished</span><span>AS220</span></div><p class="card-price"><s>$ 90.00</s>$ 70.00</p></div>
    <div class="card"><div class="card-media"><div class="media-fill fill-dark" role="img" aria-label="Rack network appliance"></div></div><p class="card-name">VRL-OEAJK821-A-K9</p><div class="card-meta"><span>Referbished</span><span>AS220</span></div><p class="card-price"><s>$ 90.00</s>$ 70.00</p></div>
  </div>
</section>

<section class="most-viewed">
  <h2 class="section-title">MOST VIEWED PRODUCTS</h2>
  <div class="rule"></div>
  <div class="grid">
    <div class="card"><div class="card-media"><div class="media-fill fill-green" role="img" aria-label="Voice processing memory module"></div></div><p class="card-name">VDSP2-16 Refurbished</p></div>
    <div class="card"><div class="card-media"><div class="media-fill fill-green" role="img" aria-label="ATM interface card"></div></div><p class="card-name">VXM-ATM-4T1/E1 Brand New</p></div>
    <div class="card"><div class="card-media"><div class="media-fill fill-green" role="img" aria-label="Network interface board"></div></div><p class="card-name">VLC-LH-SM New Sealed</p></div>
    <div class="card"><div class="card-media"><div class="media-fill fill-green" role="img" aria-label="Voice processing memory module"></div></div><p class="card-name">VDSP2-48 Refurbished</p></div>
  </div>
</section>

<section class="quote">
  <div class="quote-copy">
    <h2 class="quote-title">REQUEST A QUOTE</h2>
    <p class="quote-text">Call today for a great price on new and used networking equipment.</p>
    <div class="contact-row phone"><span class="icon-circle"><svg width="18" height="18" viewBox="0 0 18 18"><path d="M4 1.5l3 3.5-1.6 2a9 9 0 0 0 5.6 5.6l2-1.6 3.5 3-1.8 2.5C7.5 16 2 10.5 1.5 3.3z" fill="currentColor"/></svg></span>(061) 02 5550 1470</div>
    <p class="or-mail">Or mail to:</p>
    <div class="contact-row mail"><span class="icon-circle"><svg width="18" height="14" viewBox="0 0 18 14"><rect x="1" y="1" width="16" height="12" rx="1" fill="none" stroke="currentColor" stroke-width="1.8"/><path d="M1.5 1.8L9 8l7.5-6.2" fill="none" stroke="currentColor" stroke-width="1.8"/></svg></span>netkestrel.sales@kestrelmail.com</div>
  </div>
  <div class="quote-person" role="img" aria-label="Customer support agent with headset"></div>
  <div class="promo">
    <div class="promo-visual" role="img" aria-label="Group of network devices"></div>
    <div class="promo-title">SAVE UPTO 95%</div>
    <div class="promo-sub">ON VORLAN</div>
    <p class="promo-note">Same day shipment for most items<br>One year end user warranty</p>
  </div>
</section>

<nav class="link-bar">
  <a>WARRANTY<svg width="12" height="20" viewBox="0 0 12 20"><path d="M2 2l8 8-8 8" fill="none" stroke="#fff" stroke-width="3"/></svg></a>
  <a class="blue">PRIVACY STATEMENT<svg width="12" height="20" viewBox="0 0 12 20"><path d="M2 2l8 8-8 8" fill="none" stroke="#fff" stroke-width="3"/></svg></a>
  <a>TERMS OF TRADE<svg width="12" height="20" viewBox="0 0 12 20"><path d="M2 2l8 8-8 8" fill="none" stroke="#fff" stroke-width="3"/></svg></a>
</nav>

<footer class="site-footer">
  <div class="footer-cols">
    <div class="footer-col">
      <h3 class="footer-title">ABOUT US</h3><div class="footer-rule"></div>
      <p class="footer-text">Nemo enim ipsam voluptatem quia voluptas sit aspernatur aut odit aut fugit, sed quia conse quuntur magni dolores eos qui ratione volupta tem sequi nesciunt.</p>
      <p class="footer-text">Sed quia conse quuntur magni dolores eos qui ratione volupta tem sequi nesciunt.</p>
      <div class="pay"><span style="background:#1a3a8c"></span><span style="background:#d9402b"></span><span style="background:#2a7fc7"></span><span style="background:#2f6fb5"></span></div>
    </div>
    <div class="footer-col">
      <h3 class="footer-title">CONTACT US</h3><div class="footer-rule"></div>
      <ul class="footer-list">
        <li><span class="ic"><svg width="12" height="14" viewBox="0 0 12 14"><path d="M6 13S1 8 1 5a5 5 0 0 1 10 0c0 3-5 8-5 8z" fill="none" stroke="#333" stroke-width="1.4"/><circle cx="6" cy="5" r="1.6" fill="#333"/></svg></span><span class="txt">Unit 9/12 Harbour Lane Kestrel Park,<br>NSW 2199</span></li>
        <li><span class="ic"><svg width="12" height="12" viewBox="0 0 18 18"><path d="M4 1.5l3 3.5-1.6 2a9 9 0 0 0 5.6 5.6l2-1.6 3.5 3-1.8 2.5C7.5 16 2 10.5 1.5 3.3z" fill="#333"/></svg></span><span class="txt">(+61) 2 5550 1470/04 5550 2288</span></li>
        <li><span class="ic"><svg width="14" height="14" viewBox="0 0 14 14"><circle cx="7" cy="7" r="5.5" fill="none" stroke="#333" stroke-width="1.4"/><path d="M7 3.5V7h3" fill="none" stroke="#333" stroke-width="1.4"/></svg></span><span class="txt">8.30 am - 5.30 pm / Mon - Fri (UTC + 10)</span></li>
        <li><span class="ic"><svg width="14" height="11" viewBox="0 0 18 14"><rect x="1" y="1" width="16" height="12" rx="1" fill="none" stroke="#333" stroke-width="1.8"/><path d="M1.5 1.8L9 8l7.5-6.2" fill="none" stroke="#333" stroke-width="1.8"/></svg></span><span class="txt">sales@netkestrel.com.au</span></li>
      </ul>
    </div>
    <div class="footer-col">
      <h3 class="footer-title">WHY US</h3><div class="footer-rule"></div>
      <ul class="footer-list">
        <li><span class="ic"><svg width="10" height="14" viewBox="0 0 10 14"><text x="5" y="12" text-anchor="middle" font-size="13" font-family="Roboto,sans-serif" fill="#333">$</text></svg></span><span class="txt">100% wholesale price</span></li>
        <li><span class="ic"><svg width="14" height="14" viewBox="0 0 14 14"><circle cx="7" cy="7" r="4" fill="none" stroke="#333" stroke-width="2.4" stroke-dasharray="2 1.4"/><circle cx="7" cy="7" r="1.5" fill="#333"/></svg></span><span class="txt">100% quality assurance</span></li>
        <li><span class="ic"><svg width="12" height="12" viewBox="0 0 12 12"><circle cx="3" cy="3" r="1.8" fill="#333"/><circle cx="9" cy="9" r="1.8" fill="#333"/><line x1="10" y1="1" x2="2" y2="11" stroke="#333" stroke-width="1.6"/></svg></span><span class="txt">Free Support</span></li>
        <li><span class="ic"><svg width="14" height="14" viewBox="0 0 14 14"><path d="M12 7A5 5 0 1 1 10 3" fill="none" stroke="#333" stroke-width="1.6"/><path d="M9 1l2.5 2L9 5" fill="none" stroke="#333" stroke-width="1.6"/></svg></span><span class="txt">100% money back gurantee</span></li>
      </ul>
    </div>
  </div>
  <div class="footer-bottom">Copyrights @ NetKestrel. All Rights Reserved.</div>
</footer>

</body>
</html>
```